Book Cover: Quiet Harbor: Small Ceremonies For The Restless Soul

I would like a full cover spread- front, back and spine as well as a stand alone front cover for Kindle for the book. Design a cover that mirrors the profound depth and dynamic energy of 'Quiet Harbor.' Envision a visual tapestry that draws readers into a transformative journey, where spirituality and self-care unite. Explore vibrant colors, intricate textures, and a sense of inner radiance that beckons readers to explore the book's rich wisdom within. See images for design inspiration attached. Even though some of the images are cartoon, I'd like the cover to be more serious than playful and very elegant.

About this book (back cover copy)
Are you ready to embark on a transformative journey and elevate your daily existence? "Quiet Harbor" is a treasure trove of practical yet profound rituals and wisdom from renowned self-care, healing, and spirituality experts.

Within these pages, you'll uncover a tapestry of guidance and insight from some of the world's most respected mentors. Their collective wisdom is your key to creating a sacred sanctuary within your everyday life.

From invigorating morning rituals to meditative practices, empowering affirmations, and transformative energy healing, you'll find a rich tapestry of tools to nurture a deeper connection with yourself and the universe.

Whether you're a seasoned practitioner or a newcomer to the world of self-care and spirituality, "Quiet Harbor" is your trusted companion on the journey to transform your life and elevate your daily experience. Open this book today and start your sacred, fulfilling adventure.

Colors
0094D4
00A9DD
6FCCEA
C7EBF8
E9F6FB
E54698
E96AAD
F1A4CE
F9D9EA
FCEFF6
6B429C
8869AF
B7A5CE
E3DAEB
F3F0F8

Requirements
Must have
• Title: Quiet Harbor: Subtitle: Small Ceremonies For The Restless Soul Name of Publisher: Lantern Bough Publishing- Logo on the back Back cover copy

```html
<!DOCTYPE html>
<html lang="en">
<head>
<meta charset="utf-8">
<title>Quiet Harbor – Full Cover Spread</title>
<link rel="stylesheet" href="https://fonts.googleapis.com/css2?family=Allura&family=Cormorant+Garamond:ital,wght@0,500;1,400&family=Source+Serif+4:ital,opsz,wght@0,8..60,400;0,8..60,600;1,8..60,400&family=Jost:wght@300&family=Roboto:wght@400;700&display=swap">
<style>
  :root {
    --stage: #1e1e1e;
    --paper: #ffffff;
    --teal: #4e8e93;
    --teal-deep: #3f7c80;
    --teal-soft: #a9cfd1;
    --mist: #dcebec;
    --pink: #f29db2;
    --pink-soft: #fbdde5;
    --ink: #1d1d1d;
    --grey: #777777;
    --box: #efefef;
  }
  * { margin: 0; padding: 0; box-sizing: border-box; }
  html, body {
    width: 1200px; height: 1200px; overflow: hidden;
    background: var(--stage);
  }
  .spread {
    position: absolute; left: 20px; top: 188px;
    width: 1160px; height: 823px;
    background: var(--paper);
    overflow: hidden;
  }
  .panel { position: absolute; top: 0; height: 100%; }
  .back  { left: 0; width: 547px; }
  .spine { left: 547px; width: 55px; }
  .front { left: 602px; width: 558px; }

  .art { position: absolute; }

  /* back artwork */
  .back .art-blossom {
    left: 0; top: 0; width: 130px; height: 170px;
    background: radial-gradient(ellipse at 30% 35%, var(--pink-soft) 0%, rgba(251,221,229,.5) 45%, rgba(255,255,255,0) 75%);
  }
  .back .art-top-leaves {
    left: 120px; top: 0; width: 330px; height: 90px;
    background: radial-gradient(ellipse at 50% 10%, rgba(220,235,236,.8) 0%, rgba(255,255,255,0) 70%);
  }
  .back .art-foliage {
    left: 0; top: 270px; width: 200px; height: 553px;
    background:
      radial-gradient(ellipse at 25% 85%, rgba(63,124,128,.85) 0%, rgba(78,142,147,.45) 35%, rgba(255,255,255,0) 65%),
      radial-gradient(ellipse at 15% 55%, rgba(88,170,140,.55) 0%, rgba(255,255,255,0) 45%),
      radial-gradient(ellipse at 20% 20%, rgba(169,207,209,.6) 0%, rgba(255,255,255,0) 55%);
  }

  .back-title {
    position: absolute; left: 150px; top: 58px; width: 260px; height: 150px;
    font-family: "Allura", cursive;
  }
  .back-title .word-main {
    position: absolute; left: 0; top: 0;
    font-size: 92px; line-height: 1; color: var(--teal);
  }
  .back-title .word-accent {
    position: absolute; left: 70px; top: 62px;
    font-size: 62px; line-height: 1; color: var(--pink);
  }
  .back-subtitle {
    position: absolute; left: 60px; width: 434px; top: 212px;
    text-align: center;
    font-family: "Cormorant Garamond", serif;
    font-size: 21px; color: var(--grey);
  }
  .back-subtitle em { font-style: italic; font-weight: 400; }
  .back-subtitle span { font-weight: 500; }

  .blurb {
    position: absolute; left: 68px; width: 420px; top: 244px;
    font-family: "Source Serif 4", serif;
    font-size: 13.4px; line-height: 19px; color: var(--ink);
    text-align: center;
  }
  .blurb p + p { margin-top: 19px; }
  .blurb strong { font-weight: 600; }

  .publisher {
    position: absolute; left: 176px; top: 712px; width: 160px;
    text-align: center;
    font-family: "Jost", sans-serif; font-weight: 300;
    color: var(--ink); font-size: 19px; line-height: 28px;
  }
  .publisher .line-2 { letter-spacing: 2px; display: block; }
  .barcode-space {
    position: absolute; left: 345px; top: 697px;
    width: 143px; height: 86px; background: var(--box);
  }

  /* spine */
  .spine-text {
    position: absolute; left: 0; top: 36px; width: 55px; height: 770px;
    writing-mode: vertical-rl;
    display: flex; align-items: center; gap: 12px;
    white-space: nowrap;
  }
  .spine-title { font-family: "Allura", cursive; font-size: 44px; line-height: 1; }
  .spine-title .main { color: var(--teal); }
  .spine-title .accent { color: var(--pink); }
  .spine-subtitle {
    font-family: "Cormorant Garamond", serif; font-size: 17px; color: var(--grey);
  }
  .spine-subtitle em { font-style: italic; }
  .spine-publisher {
    font-family: "Roboto", sans-serif; font-size: 15px; color: var(--teal-deep);
  }
  .spine-publisher b { font-weight: 700; }

  /* front artwork */
  .front .art-florals {
    left: 120px; top: 0; width: 438px; height: 400px;
    background:
      radial-gradient(ellipse at 85% 15%, rgba(242,157,178,.85) 0%, rgba(251,221,229,.6) 22%, rgba(255,255,255,0) 45%),
      radial-gradient(ellipse at 65% 40%, rgba(78,142,147,.8) 0%, rgba(169,207,209,.5) 40%, rgba(255,255,255,0) 70%),
      radial-gradient(ellipse at 30% 25%, rgba(220,235,236,.8) 0%, rgba(255,255,255,0) 60%);
  }
  .front .art-figure {
    left: 70px; top: 290px; width: 200px; height: 250px;
    border-radius: 46% 46% 30% 30%;
    background: linear-gradient(180deg, rgba(78,142,147,.9) 0%, rgba(78,142,147,.75) 70%, rgba(78,142,147,0) 100%);
  }
  .front .art-sprigs {
    left: 280px; top: 560px; width: 278px; height: 263px;
    background: radial-gradient(ellipse at 60% 55%, rgba(200,222,215,.7) 0%, rgba(255,255,255,0) 70%);
  }
  .front .art-petals {
    left: 120px; top: 740px; width: 170px; height: 83px;
    background: radial-gradient(ellipse at 50% 80%, rgba(251,221,229,.7) 0%, rgba(255,255,255,0) 70%);
  }

  .front-subtitle {
    position: absolute; left: 312px; top: 418px; width: 210px;
    text-align: center;
    font-family: "Cormorant Garamond", serif; color: var(--grey);
    font-size: 23px; line-height: 29px;
  }
  .front-subtitle em { font-style: italic; font-weight: 400; display: block; }
  .front-subtitle span { font-weight: 500; }

  .front-title { position: absolute; left: 0; top: 0; width: 558px; height: 823px; font-family: "Allura", cursive; }
  .front-title .word-main {
    position: absolute; left: 26px; top: 470px;
    font-size: 190px; line-height: 1; color: var(--teal);
  }
  .front-title .word-accent {
    position: absolute; left: 130px; top: 600px;
    font-size: 118px; line-height: 1; color: var(--pink);
  }
</style>
</head>
<body>
<main class="spread">

  <section class="panel back">
    <div class="art art-blossom" role="img" aria-label="Soft watercolour pink blossom"></div>
    <div class="art art-top-leaves" role="img" aria-label="Faint watercolour leaves along the top edge"></div>
    <div class="art art-foliage" role="img" aria-label="Watercolour teal and green leaves rising along the left edge"></div>

    <h2 class="back-title">
      <span class="word-main">Quiet</span>
      <span class="word-accent">Harbor</span>
    </h2>
    <p class="back-subtitle"><em>Small Ceremonies for</em> <span>The Restless Soul</span></p>

    <div class="blurb">
      <p><strong>Are you ready to embark on a transformative journey and elevate your daily existence?</strong> <em>"Quiet Harbor"</em> is a treasure trove of practical yet profound rituals and wisdom from renowned self-care, healing, and spirituality experts.</p>
      <p>Within these pages, you'll uncover a tapestry of guidance and insight from some of the world's most respected mentors. Their collective wisdom is your key to creating a sacred sanctuary within your everyday life.</p>
      <p>From invigorating morning rituals to meditative practices, empowering affirmations, and transformative energy healing, you'll find a rich tapestry of tools to nurture a deeper connection with yourself and the universe.</p>
      <p>Whether you're a seasoned practitioner or a newcomer to the world of self-care and spirituality, "Quiet Harbor" is your trusted companion on the journey to transform your life and elevate your daily experience. Open this book today and start your sacred, fulfilling adventure.</p>
    </div>

    <div class="publisher">Lantern Bough <span class="line-2">Publishing</span></div>
    <div class="barcode-space"></div>
  </section>

  <section class="panel spine">
    <div class="spine-text">
      <span class="spine-title"><span class="main">Quiet</span> <span class="accent">Harbor</span></span>
      <span class="spine-subtitle"><em>Small Ceremonies for</em> The Restless Soul</span>
      <span class="spine-publisher"><b>Lantern Bough</b> Publishing</span>
    </div>
  </section>

  <section class="panel front">
    <div class="art art-florals" role="img" aria-label="Watercolour teal leaves and pink blossoms from the top right corner"></div>
    <div class="art art-sprigs" role="img" aria-label="Pale eucalyptus sprigs"></div>
    <div class="art art-petals" role="img" aria-label="Faint pink blossom at the bottom edge"></div>
    <div class="art art-figure" role="img" aria-label="Teal silhouette of a woman in profile with flowers in her hair"></div>

    <p class="front-subtitle"><em>Small Ceremonies for</em><span>The Restless Soul</span></p>

    <h1 class="front-title">
      <span class="word-main">Quiet</span>
      <span class="word-accent">Harbor</span>
    </h1>
  </section>

</main>
</body>
</html>
```